Cedar Brook Stables, LLC

Equestrian business card to promote equine retirement, farm sitting, short term board. Located in Aiken, SC.
Updates
Updated color schemes.
Contact Information for Business Card
Contact info, description of work.
Colors
0094D4
00A9DD
6FCCEA
C7EBF8
E9F6FB
59FF00
82FF00
B8FF75
E3FFCB
F4FFEA
F0912C
F2A743
F7CA91
FBE8D2
FDF5EE

```html
<!DOCTYPE html>
<html lang="en">
<head>
<meta charset="UTF-8">
<title>Cedar Brook Stables, LLC – Business Card</title>
<link href="https://fonts.googleapis.com/css2?family=Montserrat:wght@600;700&family=Poppins:wght@400;500&display=swap" rel="stylesheet">
<style>
  :root{
    --farm-green:#067206;
    --farm-green-dark:#055a05;
    --sun-yellow:#fdb913;
    --sun-orange:#f0912c;
    --ink:#222222;
    --ink-soft:#444444;
    --paper:#ffffff;
    --backdrop:#ece9e4;
  }
  *{margin:0;padding:0;box-sizing:border-box}
  html,body{width:1200px;height:900px;overflow:hidden;background:var(--backdrop)}
  .canvas{position:relative;width:1200px;height:900px}

  .card{position:absolute;width:640px;height:366px;overflow:hidden;
        box-shadow:0 10px 24px rgba(0,0,0,.22)}

  /* Front */
  .card-front{left:130px;top:48px;background:var(--farm-green);color:var(--paper)}
  .brand{display:flex;align-items:center;gap:14px}
  .brand-dot{width:34px;height:34px;border-radius:50%;flex:none}
  .brand-name{font-family:"Montserrat",sans-serif;font-weight:700;letter-spacing:.5px;line-height:1.15}
  .card-front .brand{position:absolute;left:0;right:0;top:120px;justify-content:center}
  .card-front .brand-dot{background:var(--sun-yellow)}
  .card-front .brand-name{font-size:30px;color:var(--paper)}
  .services{position:absolute;left:0;right:0;bottom:58px;text-align:center;
            font-family:"Montserrat",sans-serif;font-weight:600;font-size:15px;letter-spacing:.8px}
  .services .sep{display:inline-block;width:9px;height:9px;border-radius:50%;
                 background:var(--sun-yellow);margin:0 10px;vertical-align:middle}

  /* Back */
  .card-back{left:430px;top:486px;background:var(--paper)}
  .card-back .wave{position:absolute;left:0;bottom:0;width:640px;height:180px}
  .card-back .brand{position:absolute;left:34px;top:118px;width:260px}
  .card-back .brand-dot{background:var(--farm-green)}
  .card-back .brand-name{font-size:21px;color:var(--farm-green)}
  .divider{position:absolute;left:312px;top:34px;width:1px;height:196px;background:#9a9a9a}
  .contact{position:absolute;left:336px;top:34px;font-family:"Poppins",sans-serif;color:var(--ink)}
  .person-name{font-family:"Montserrat",sans-serif;font-weight:700;font-size:24px;color:var(--farm-green);letter-spacing:.5px}
  .person-role{font-size:14px;color:var(--ink-soft);margin-bottom:14px}
  .contact-list{list-style:none}
  .contact-list li{display:flex;align-items:center;gap:10px;font-size:14px;line-height:24px}
  .contact-list svg{width:16px;height:16px;flex:none}
  .address{margin-top:16px;font-size:14px;line-height:20px;padding-left:4px}
</style>
</head>
<body>
<div class="canvas">

  <section class="card card-front">
    <div class="brand">
      <span class="brand-dot"></span>
      <span class="brand-name">CEDAR BROOK STABLES<br><small style="font-size:14px;letter-spacing:2px">LLC</small></span>
    </div>
    <p class="services">SHORT TERM BOARD<span class="sep"></span>FARM SITTING<span class="sep"></span>EQUINE RETIREMENT</p>
  </section>

  <section class="card card-back">
    <svg class="wave" viewBox="0 0 640 180" preserveAspectRatio="none">
      <path d="M0 120 C200 150 380 110 640 0 L640 180 L0 180 Z" fill="var(--farm-green)"/>
      <path d="M0 95 C180 120 330 100 470 30 C350 110 190 140 0 135 Z" fill="var(--sun-yellow)"/>
      <path d="M0 135 C190 140 350 110 470 30 C360 120 200 150 0 150 Z" fill="var(--paper)"/>
    </svg>

    <div class="brand">
      <span class="brand-dot"></span>
      <span class="brand-name">CEDAR BROOK STABLES<br><small style="font-size:12px;letter-spacing:2px">LLC</small></span>
    </div>

    <div class="divider"></div>

    <div class="contact">
      <h1 class="person-name">DANIEL HARPER</h1>
      <p class="person-role">Managing Director</p>
      <ul class="contact-list">
        <li><svg viewBox="0 0 24 24"><path fill="var(--farm-green)" d="M6.6 10.8a15 15 0 006.6 6.6l2.2-2.2a1 1 0 011-.25 11.4 11.4 0 003.6.57 1 1 0 011 1V20a1 1 0 01-1 1A17 17 0 013 4a1 1 0 011-1h3.5a1 1 0 011 1c0 1.25.2 2.45.57 3.6a1 1 0 01-.25 1z"/></svg>803-555-0147</li>
        <li><svg viewBox="0 0 24 24"><path fill="var(--farm-green)" d="M2 5h20v14H2z"/><path fill="none" stroke="#fff" stroke-width="1.6" d="M2.5 5.5L12 13l9.5-7.5"/></svg>info@cedarbrook.com</li>
        <li><svg viewBox="0 0 24 24" fill="none" stroke="var(--farm-green)" stroke-width="2"><circle cx="12" cy="12" r="9.5"/><path d="M2.5 12h19M12 2.5c3 3 3 16 0 19M12 2.5c-3 3-3 16 0 19"/></svg>www.cedarbrook.com</li>
      </ul>
      <p class="address">118 Whiskey Road<br>Aiken, SC 29801</p>
    </div>
  </section>

</div>
</body>
</html>
```